Copper lark buildworks

Copper lark buildworks is a small construction company.
Who is a licenced builder, Carpenter, joiner,
working on heritage ,new build, speacial projects and sometimes furniture

Industry/Entity Type

Construction

```html
<!DOCTYPE html>
<html lang="en">
<head>
<meta charset="utf-8">
<title>Copper lark buildworks – Business Card</title>
<link href="https://fonts.googleapis.com/css2?family=Exo+2:wght@400;500&family=Lato:wght@400&display=swap" rel="stylesheet">
<style>
  :root {
    --page-bg: #d9d4cc;
    --card-top: #f4f2ee;
    --card-bottom: #e3dfd8;
    --ink: #1c1c1c;
    --green: #4f8f23;
    --green-dark: #2f6a12;
    --green-light: #6aa534;
    --swoosh: #141414;
  }
  * { margin: 0; padding: 0; box-sizing: border-box; }
  html, body { width: 1200px; height: 970px; overflow: hidden; }
  body {
    background: var(--page-bg);
    position: relative;
    font-family: "Lato", sans-serif;
  }
  .card {
    position: absolute;
    left: 80px; top: 190px;
    width: 1040px; height: 590px;
    border-radius: 26px;
    overflow: hidden;
    background: linear-gradient(180deg, var(--card-top), var(--card-bottom));
    box-shadow: 0 14px 40px rgba(0,0,0,0.18);
  }
  .card-wave { position: absolute; left: 0; top: 0; }
  .brand {
    position: absolute;
    left: 40px; top: 255px;
    width: 420px;
    display: flex; align-items: center; justify-content: center; gap: 14px;
  }
  .brand-dot {
    width: 30px; height: 30px; border-radius: 50%;
    background: var(--green); flex: none;
  }
  .brand-name {
    font-family: "Exo 2", sans-serif;
    font-weight: 500;
    font-size: 32px;
    color: var(--ink);
    white-space: nowrap;
  }
  .divider {
    position: absolute;
    left: 491px; top: 183px;
    width: 2px; height: 182px;
    background: var(--green);
  }
  .person { position: absolute; left: 572px; top: 176px; }
  .person-name {
    font-family: "Exo 2", sans-serif;
    font-size: 31px; font-weight: 500; color: var(--ink); line-height: 1.05;
  }
  .person-name .surname { color: var(--green); }
  .person-role {
    font-family: "Exo 2", sans-serif;
    font-size: 25px; color: var(--ink); line-height: 1.15;
  }
  .contacts {
    position: absolute; left: 572px; top: 264px;
    list-style: none;
  }
  .contact {
    display: flex; align-items: center; gap: 10px;
    height: 37px;
    font-size: 25px; color: var(--ink);
  }
  .contact-icon { width: 30px; height: 30px; flex: none; }
</style>
</head>
<body>
  <div class="card">
    <svg class="card-wave" width="1040" height="590" viewBox="0 0 1040 590" aria-hidden="true">
      <defs>
        <linearGradient id="band" x1="0" y1="0" x2="0" y2="1">
          <stop offset="0" stop-color="#5a9a2a"/>
          <stop offset="1" stop-color="#3f7d1a"/>
        </linearGradient>
      </defs>
      <path d="M0 468 C 220 560, 560 570, 1040 458 L1040 590 L0 590 Z" fill="url(#band)"/>
      <path d="M0 462 C 230 548, 560 556, 1040 450 L1040 458 C 560 570, 220 560, 0 468 Z" fill="#ece8e2"/>
      <path d="M30 462 C 240 540, 520 548, 1025 446 C 560 532, 250 548, 30 462 Z" fill="var(--swoosh)" stroke="var(--swoosh)" stroke-width="3"/>
    </svg>

    <div class="brand">
      <span class="brand-dot"></span>
      <span class="brand-name">Copper lark buildworks</span>
    </div>

    <div class="divider"></div>

    <div class="person">
      <div class="person-name">Marcus <span class="surname">Hale</span></div>
      <div class="person-role">President</div>
    </div>

    <ul class="contacts">
      <li class="contact">
        <svg class="contact-icon" viewBox="0 0 30 30" aria-hidden="true">
          <circle cx="15" cy="15" r="13" fill="none" stroke="var(--green)" stroke-width="2.5"/>
          <rect x="10.5" y="7.5" width="9" height="15" rx="1.5" fill="none" stroke="var(--green)" stroke-width="2"/>
          <circle cx="15" cy="19.5" r="1" fill="var(--green)"/>
        </svg>
        <span>0491570156</span>
      </li>
      <li class="contact">
        <svg class="contact-icon" viewBox="0 0 30 30" aria-hidden="true">
          <circle cx="15" cy="15" r="14" fill="var(--green)"/>
          <rect x="8" y="10" width="14" height="10" fill="none" stroke="#fff" stroke-width="1.8"/>
          <path d="M8 10 L15 16 L22 10" fill="none" stroke="#fff" stroke-width="1.8"/>
        </svg>
        <span>info@copperlarkbuild.com</span>
      </li>
      <li class="contact">
        <svg class="contact-icon" viewBox="0 0 30 30" aria-hidden="true">
          <circle cx="15" cy="15" r="14" fill="var(--green)"/>
          <circle cx="15" cy="15" r="8" fill="none" stroke="#fff" stroke-width="1.6"/>
          <ellipse cx="15" cy="15" rx="3.5" ry="8" fill="none" stroke="#fff" stroke-width="1.4"/>
          <line x1="7" y1="15" x2="23" y2="15" stroke="#fff" stroke-width="1.4"/>
        </svg>
        <span>www.copperlarkbuild.com</span>
      </li>
    </ul>
  </div>
</body>
</html>
```